Ridgeline Orchards Organic Cherry POS card 7x11

We are wanting to create a one-sided 7 x 11 organic cherry card that is eye catching and informative.This should be clear and easy to read and not cluttered. We use these cards as a display in grocery stores, demo stands, and other events to market Organic Ridgeline Sweet Orchards. We have a few facts that we would like displayed on the card (see attachment).

Target Market(s)

Consumers

Industry/Entity Type

Agriculture

Requirements
Must have
• Natural color palettes
• Easy to read
• Ridgeline Orchards
Nice to have
• Unique, realistic cherry design

```html
<!DOCTYPE html>
<html lang="en">
<head>
<meta charset="utf-8">
<title>Ridgeline Orchards Organic Cherry Card</title>
<link rel="stylesheet" href="https://fonts.googleapis.com/css2?family=Questrial&family=Satisfy&display=swap">
<style>
  :root {
    --page: #ffffff;
    --bg-top: #8c7862;
    --bg-mid: #7a5a4e;
    --bg-bottom: #6b3a3c;
    --cherry-dark: #3e0a12;
    --cherry-mid: #7a1424;
    --cherry-light: #a8303e;
    --text-light: #e6dcd6;
    --frame: rgba(225, 212, 205, 0.75);
    --ink: #1d1416;
    --white: #ffffff;
  }
  * { margin: 0; padding: 0; box-sizing: border-box; }
  html, body { width: 1200px; height: 880px; overflow: hidden; background: var(--page); }
  .canvas { position: relative; width: 1200px; height: 880px; background: var(--page); }
  .card {
    position: absolute; left: 0; top: 58px; width: 1200px; height: 764px; overflow: hidden;
    background: linear-gradient(180deg, var(--bg-top) 0%, var(--bg-mid) 45%, var(--bg-bottom) 100%);
  }
  .cherry-photo {
    position: absolute; left: 560px; top: 0; width: 640px; height: 700px;
    background:
      radial-gradient(ellipse 150px 175px at 175px 450px, var(--cherry-light) 0%, var(--cherry-mid) 45%, rgba(62,10,18,0) 100%),
      radial-gradient(ellipse 150px 170px at 420px 420px, var(--cherry-mid) 0%, var(--cherry-dark) 55%, rgba(62,10,18,0) 100%);
  }
  .brand {
    position: absolute; left: 390px; top: 30px; display: flex; align-items: center; gap: 16px;
  }
  .brand-mark { width: 46px; height: 46px; border-radius: 50%; background: var(--cherry-mid); }
  .brand-name {
    font-family: "Questrial", sans-serif; font-size: 42px; color: var(--ink); letter-spacing: 2px;
  }
  .frame { position: absolute; left: 0; top: 0; }
  .facts {
    position: absolute; left: 50px; top: 0;
    font-family: "Questrial", sans-serif; color: var(--text-light);
    font-size: 28px; letter-spacing: 10px; text-transform: uppercase; line-height: 1;
  }
  .facts span { position: absolute; left: 0; white-space: nowrap; }
  .benefits-ring { position: absolute; left: 0; top: 0; }
  .benefits {
    position: absolute; left: 700px; top: 0; width: 440px;
    font-family: "Satisfy", cursive; color: var(--white); font-size: 25px; text-align: center; line-height: 1;
  }
  .benefits span { position: absolute; left: 0; width: 440px; }
</style>
</head>
<body>
<div class="canvas">
  <section class="card">
    <div class="cherry-photo" role="img" aria-label="Close-up photograph of two glossy dark red cherries hanging from their stems, dotted with water drops"></div>

    <svg class="frame" width="1200" height="764" viewBox="0 0 1200 764">
      <rect x="20" y="160" width="1160" height="560" fill="none" stroke="var(--frame)" stroke-width="4" stroke-dasharray="22 14"/>
    </svg>

    <div class="brand">
      <span class="brand-mark"></span>
      <span class="brand-name">Ridgeline Orchards</span>
    </div>

    <div class="facts">
      <span style="top:200px">Organic</span>
      <span style="top:244px">Ridgeline Orchards</span>
      <span style="top:302px">Make up 1/3</span>
      <span style="top:360px">of the nation's</span>
      <span style="top:404px">production.</span>
      <span style="top:466px">Washington State</span>
      <span style="top:510px">is the nation's</span>
      <span style="top:554px">largest producer</span>
      <span style="top:598px">&nbsp;of organic</span>
      <span style="top:640px">cherries.</span>
    </div>

    <svg class="benefits-ring" width="1200" height="764" viewBox="0 0 1200 764">
      <circle cx="920" cy="550" r="146" fill="none" stroke="rgba(255,255,255,0.55)" stroke-width="4"/>
    </svg>

    <div class="benefits">
      <span style="top:412px">Health benefits:</span>
      <span style="top:456px">fat free</span>
      <span style="top:496px">source of vitamin C</span>
      <span style="top:539px">a natural anti-inflammatory</span>
      <span style="top:582px">source of potassium</span>
      <span style="top:626px">source of melatonin</span>
    </div>
  </section>
</div>
</body>
</html>
```